Qvx Brightforge Website

All the descriptions are available in the attached file. The designer has to structure the website and find the right images and icons. The website should look modern and avoid using images of real humans rather use animated images. Please note that the design should include home page, all the 4 services page , the contact us would be at the bottom of home page.

```html
<!DOCTYPE html>
<html lang="en">
<head>
<meta charset="utf-8">
<title>Qvx Brightforge</title>
<link href="https://fonts.googleapis.com/css2?family=Michroma&family=Lato:wght@400;700&display=swap" rel="stylesheet">
<style>
:root{
  --navy-deep:#061a33;
  --blue:#0a6fe0;
  --blue-soft:#cfe2f7;
  --orange:#ff9a05;
  --ink:#111;
  --text:#333;
  --muted:#7a7a7a;
  --panel:#f3f3f3;
  --foot:#f8f8f8;
  --line:#e2e2e2;
  --white:#fff;
}
*{margin:0;padding:0;box-sizing:border-box}
html,body{width:1200px;height:3139px;overflow:hidden}
body{position:relative;font-family:"Lato",sans-serif;color:var(--text);background:var(--white)}
.abs{position:absolute}
.display{font-family:"Michroma",sans-serif;text-transform:uppercase;color:var(--ink);line-height:1.15}

/* hero */
.hero{left:0;top:0;width:1200px;height:652px;background:radial-gradient(ellipse at 80% 50%,#1a5fae 0%,#0c3563 40%,var(--navy-deep) 100%)}
.brand{left:111px;top:34px;display:flex;align-items:center;gap:8px;color:var(--white);font-family:"Michroma",sans-serif;font-size:17px}
.brand .mark{width:10px;height:10px;background:var(--orange)}
.nav{right:113px;top:48px;display:flex;gap:31px}
.nav a{color:var(--white);text-decoration:none;font-size:15px}
.hero-title{left:109px;top:202px;font-size:38px;color:var(--white);white-space:nowrap}
.hero-sub{left:111px;top:272px;width:470px;font-size:16.5px;line-height:30px;color:var(--white)}
.hero-art{left:690px;top:110px;width:400px;height:511px;border-radius:50%;background:radial-gradient(circle,#6fd3ff 0%,#2a7fe0 35%,rgba(20,60,140,0) 70%)}

/* section headings */
.sec-head{font-size:34px;white-space:nowrap}
.sec-head.center{left:0;width:1200px;text-align:center}

/* services */
.card{width:270px;text-align:center}
.card h3{font-family:"Michroma",sans-serif;font-size:18px;line-height:26px;color:var(--ink);text-transform:uppercase}
.card .bar{width:38px;height:3px;background:var(--blue);margin:12px auto 22px}
.card p{font-size:15px;line-height:30px;color:var(--text)}
.card .icon{width:72px;height:72px;border-radius:50%;background:var(--blue-soft);margin:0 auto 30px}
.card .more{display:inline-block;margin-top:18px;font-family:"Michroma",sans-serif;font-size:14px;color:var(--blue);text-transform:uppercase}
.card.featured{background:var(--white);border-radius:56px;box-shadow:0 8px 36px rgba(0,0,0,.08);padding:34px 22px 0;height:400px;width:324px}
.card.featured .icon{background:var(--orange)}
.card.featured .bar{background:var(--orange)}
.card.featured .more{color:var(--orange);margin-top:12px}
.arrow{width:22px;height:22px;border-radius:50%;display:flex;align-items:center;justify-content:center}

/* about */
.about{left:0;top:1342px;width:1200px;height:516px;background:var(--panel)}
.about-art{left:107px;top:65px;width:478px;height:353px;border-radius:40% 50% 45% 50%;background:linear-gradient(135deg,#e6e6e6,#4aa8f2 55%,#1a6fd6)}
.about-text{left:636px;top:130px;width:452px;font-size:14.4px;line-height:26.6px;text-align:justify}
.btn{display:flex;align-items:center;justify-content:center;border-radius:30px;color:var(--white);font-family:"Michroma",sans-serif;text-transform:uppercase}
.btn.orange{background:var(--orange)}
.btn.blue{background:var(--blue)}

/* contact */
.lead{left:0;width:1200px;text-align:center;font-size:15.5px;line-height:25px}
.info-label{font-family:"Michroma",sans-serif;font-size:15px;color:var(--ink);text-transform:uppercase}
.info-item{display:flex;gap:14px}
.info-item svg{margin-top:4px;flex:none}
.info-item p{font-size:15.5px;line-height:26px}
.field{left:544px;width:490px;height:57px;background:var(--white);box-shadow:0 6px 16px rgba(0,0,0,.07);padding:0 30px;display:flex;align-items:center;font-size:15.5px;color:var(--muted)}

/* newsletter & footer */
.footer-bg{left:0;top:2520px;width:1200px;height:619px;background:var(--foot)}
.news-title{left:0;top:2590px;width:1200px;text-align:center;font-size:31px;white-space:nowrap}
.news-input{left:237px;top:2665px;width:540px;height:54px;border-radius:30px;background:#ececec;padding-left:32px;display:flex;align-items:center;font-size:17px;color:#444}
.rule{left:111px;width:977px;height:1px;background:var(--line)}
.foot-head{font-family:"Michroma",sans-serif;font-size:15px;color:var(--ink);text-transform:uppercase}
.foot-list{font-size:15.5px;line-height:30px;color:var(--text)}
.foot-row{display:flex;gap:8px;align-items:flex-start}
.foot-row svg{margin-top:8px;flex:none}
.social{display:flex;gap:10px}
.social span{width:27px;height:27px;border-radius:50%;background:#f5d5a8}
.social span:first-child{background:var(--blue)}
.copy{left:0;top:3074px;width:1200px;text-align:center;font-size:15.5px}
.copy a{color:var(--orange)}
</style>
</head>
<body>

<header class="abs hero">
  <div class="abs brand"><span class="mark"></span>Qvx Brightforge</div>
  <nav class="abs nav"><a>Home</a><a>Services</a><a>Products</a><a>Blog</a><a>Contact us</a></nav>
  <div class="abs hero-art" role="img" aria-label="Glowing isometric server block illustration with neon rings"></div>
  <h1 class="abs display hero-title">Qvx Brightforge</h1>
  <p class="abs display hero-sub">Empower your digital journey with our advanced IT solutions. From data to web and mobile apps, we've got you covered.</p>
</header>

<section>
  <h2 class="abs display sec-head center" style="top:730px">Our Services</h2>

  <div class="abs arrow" style="left:43px;top:1032px;background:var(--orange)"><svg width="10" height="10" viewBox="0 0 10 10"><path d="M6.5 2 3.5 5l3 3" stroke="#fff" stroke-width="1.6" fill="none"/></svg></div>
  <div class="abs arrow" style="left:1129px;top:1032px;background:#ddd"><svg width="10" height="10" viewBox="0 0 10 10"><path d="M3.5 2l3 3-3 3" stroke="#fff" stroke-width="1.6" fill="none"/></svg></div>

  <article class="abs card" style="left:127px;top:858px">
    <div class="icon" role="img" aria-label="Data analytics icon"></div>
    <h3>Data Analytics</h3><div class="bar"></div>
    <p>At Qvx Brightforge, our proficiency consists of linking your leadership team's objectives with the relevant data that holds significance.</p>
    <span class="more">Learn more ➜</span>
  </article>

  <article class="abs card featured" style="left:425px;top:816px">
    <div class="icon" role="img" aria-label="Web development icon"></div>
    <h3>Web Development</h3><div class="bar"></div>
    <p>At Qvx Brightforge, we are a trailblazing web development company committed to delivering cutting-edge digital solutions that empower businesses to excel in the ever-evolving online landscape.</p>
    <span class="more">Learn more ➜</span>
  </article>

  <article class="abs card" style="left:781px;top:858px">
    <div class="icon" role="img" aria-label="Mobile app development icon"></div>
    <h3>Mobile App Development</h3><div class="bar"></div>
    <p>At Qvx Brightforge, we are a pioneering mobile app development company dedicated to crafting exceptional digital experiences...</p>
    <span class="more">Learn more ➜</span>
  </article>
</section>

<section class="abs about">
  <div class="abs about-art" role="img" aria-label="Isometric illustration of dashboards, charts and a laptop"></div>
  <h2 class="abs display sec-head" style="left:676px;top:68px">About Us</h2>
  <p class="abs about-text">We are a forward-thinking IT consulting firm specializing in providing cutting-edge data analytics, web application development, and mobile app development services.Our passion for innovation and technology drives us to deliver tailor-made solutions that empower businesses to thrive in the digital landscape. We take pride in our ability to collaborate with early-stage startups as their technology partner, helping them navigate the challenges of launching and scaling their ventures.</p>
  <div class="abs btn orange" style="left:632px;top:357px;width:145px;height:53px;font-size:14px">Lean more</div>
</section>

<section>
  <h2 class="abs display sec-head center" style="top:1940px">Contact Us</h2>
  <p class="abs lead" style="top:1994px">Lorem ipsum dolor sit amet, consectetur adipiscing elit, sed do eiusmod tempor incididunt ut labore et dolore magna aliqua.<br>Quis ipsum suspendisse ultrices gravida. Risus commodo viverra maecenas accumsan lacus vel facilisis.</p>

  <h3 class="abs display" style="left:152px;top:2112px;font-size:21px">Get a quote</h3>
  <div class="abs info-item" style="left:156px;top:2172px">
    <svg width="11" height="15" viewBox="0 0 11 15"><path d="M5.5 0A5.5 5.5 0 0 0 0 5.5C0 9.5 5.5 15 5.5 15S11 9.5 11 5.5A5.5 5.5 0 0 0 5.5 0zm0 7.5a2 2 0 1 1 0-4 2 2 0 0 1 0 4z" fill="var(--orange)"/></svg>
    <div><div class="info-label">Address</div><p>Suite 12/48 Harbour Lane,<br>Eastvale WA 6999</p></div>
  </div>
  <div class="abs info-item" style="left:156px;top:2268px">
    <svg width="13" height="13" viewBox="0 0 13 13"><path d="M2.5 0 5 3 3.6 4.6a8 8 0 0 0 4.8 4.8L10 8l3 2.5-1.6 2.2C5.5 13 0 7.5.3 1.6z" fill="var(--orange)"/></svg>
    <div><div class="info-label">Phone</div><p>+61 (08) 5550 0142 (Sales / Support)</p></div>
  </div>
  <div class="abs info-item" style="left:155px;top:2346px">
    <svg width="15" height="11" viewBox="0 0 15 11"><rect width="15" height="11" rx="1" fill="var(--orange)"/><path d="M0 1l7.5 5L15 1" stroke="#fff" stroke-width="1.3" fill="none"/></svg>
    <div><div class="info-label">Email</div><p style="color:var(--blue)">hello@qvxbrightforge.example</p></div>
  </div>

  <div class="abs field" style="top:2097px">Name</div>
  <div class="abs field" style="top:2172px">Phone</div>
  <div class="abs field" style="top:2246px">Email</div>
  <div class="abs field" style="top:2320px">Messages</div>
  <div class="abs btn blue" style="left:548px;top:2412px;width:135px;height:43px;font-size:14px">Submit</div>
</section>

<div class="abs footer-bg"></div>

<section>
  <h2 class="abs display news-title">Stay informed with our latest news</h2>
  <div class="abs news-input">Enter Your Email</div>
  <div class="abs btn orange" style="left:794px;top:2665px;width:181px;height:54px;font-size:16px">Subscribe</div>
</section>

<footer>
  <div class="abs rule" style="top:2777px"></div>
  <div class="abs" style="left:111px;top:2880px;display:flex;align-items:center;gap:10px;font-family:'Michroma',sans-serif;font-size:20px;color:var(--blue)"><span style="width:14px;height:14px;background:var(--orange)"></span>Qvx Brightforge</div>

  <div class="abs" style="left:401px;top:2843px">
    <div class="foot-head">Contact info</div>
    <div class="foot-list" style="margin-top:12px">
      <div class="foot-row"><svg width="9" height="12" viewBox="0 0 11 15"><path d="M5.5 0A5.5 5.5 0 0 0 0 5.5C0 9.5 5.5 15 5.5 15S11 9.5 11 5.5A5.5 5.5 0 0 0 5.5 0z" fill="var(--blue)"/></svg><span style="line-height:25px;margin-top:2px">Suite 12/48 Harbour Lane,<br>Eastvale WA 6999</span></div>
      <div class="foot-row" style="margin-top:4px"><svg width="11" height="11" viewBox="0 0 13 13"><path d="M2.5 0 5 3 3.6 4.6a8 8 0 0 0 4.8 4.8L10 8l3 2.5-1.6 2.2C5.5 13 0 7.5.3 1.6z" fill="var(--blue)"/></svg>+61 (08) 5550 0142 (Sales / Support)</div>
      <div class="foot-row"><svg width="13" height="10" viewBox="0 0 15 11"><rect x=".6" y=".6" width="13.8" height="9.8" fill="none" stroke="var(--blue)" stroke-width="1.2"/><path d="M1 1l6.5 5L14 1" stroke="var(--blue)" stroke-width="1.2" fill="none"/></svg>hello@qvxbrightforge.example</div>
    </div>
  </div>
  <div class="abs" style="left:748px;top:2843px">
    <div class="foot-head">Help links</div>
    <div class="foot-list" style="margin-top:12px">Terms &amp; conditions<br>Privacy Policy<br>About Us<br>Support</div>
  </div>
  <div class="abs" style="left:949px;top:2843px">
    <div class="foot-head">Follow us</div>
    <div class="social" style="margin-top:20px" aria-label="Social links"><span></span><span></span><span></span><span></span></div>
  </div>

  <div class="abs rule" style="top:3035px"></div>
  <p class="abs copy">©Copyrights 2023 <a>Qvx Brightforge</a> &nbsp;|&nbsp; All Rights Reserved</p>
</footer>

</body>
</html>
```